Satchel & Sundial needs new business card design

I need a new business card design. I'm looking for out-of-the-box design which represents the freedom of being a location independent entrepreneur.
I offer coaching, retreats and trips.
I would like to see designs with and without the photo.
Colors I use are black (#000000), green (#25A796) and brown (#D7C38C)
Website satchelandsundial.example

Target Market(s)

location independent entrepreneurs, digital nomads, people looking to swap the 9 to 5 for a lifestyle business

Industry/Entity Type

Business

Contact Information for Business Card

Dorota Falkner
Your Lifestyle Business Coach, Retreat & Trip Leader
http://satchelandsundial.example
hello@satchelandsundial.example
Live a life you don't need a holiday from

Font styles to use
Serif
Sans Serif

Requirements
Must have
• One side should contain only the logo. I would also consider having the "Live a life you don't need a holiday from" on that side too (depending on how it looks)
• Please show both sides on the designs.

```html
<!DOCTYPE html>
<html lang="en">
<head>
<meta charset="utf-8">
<title>Satchel &amp; Sundial — Business Card</title>
<link rel="stylesheet" href="https://fonts.googleapis.com/css2?family=Questrial&display=swap">
<style>
  :root {
    --teal: #25A796;
    --ink: #1d1d1f;
    --black: #000000;
    --paper: #ffffff;
    --backdrop: #ece8df;
    --muted: #3a3a3a;
  }
  * { margin: 0; padding: 0; box-sizing: border-box; }
  html, body { width: 1200px; height: 1023px; overflow: hidden; background: var(--backdrop); }
  body { font-family: "Questrial", sans-serif; position: relative; }

  .card {
    position: absolute;
    left: 200px;
    width: 800px;
    height: 457px;
    box-shadow: 0 6px 18px rgba(0,0,0,.18);
    overflow: hidden;
  }
  .card--front { top: 35px; background: var(--paper); }
  .card--back { top: 532px; background: var(--teal); }

  .front-swoosh { position: absolute; inset: 0; width: 100%; height: 100%; }

  .front-brand {
    position: absolute;
    left: 40px; top: 160px;
    width: 300px;
    text-align: center;
    font-size: 40px;
    line-height: 1.1;
    color: var(--ink);
    letter-spacing: .5px;
  }

  .front-divider {
    position: absolute;
    left: 365px; top: 70px;
    width: 2px; height: 250px;
    background: var(--ink);
  }
  .front-divider::before {
    content: "";
    position: absolute;
    left: 0; top: 0;
    width: 3px; height: 60px;
    background: var(--teal);
  }

  .contact {
    position: absolute;
    left: 395px; top: 64px;
    width: 300px;
    color: var(--muted);
    font-size: 15px;
    line-height: 1.4;
  }
  .contact__name { color: var(--teal); font-size: 26px; line-height: 1.2; margin-bottom: 4px; }
  .contact__role { margin-bottom: 20px; }
  .contact__list { list-style: none; margin-bottom: 20px; }
  .contact__list li { display: flex; align-items: center; gap: 10px; white-space: nowrap; }
  .contact__list svg { width: 14px; height: 14px; flex: none; }

  .back-brand {
    position: absolute;
    left: 0; right: 0; top: 170px;
    text-align: center;
    color: var(--paper);
    font-size: 62px;
    letter-spacing: 1px;
  }
  .back-tagline {
    position: absolute;
    left: 40px; bottom: 36px;
    color: var(--paper);
    font-size: 17px;
    letter-spacing: .3px;
  }
</style>
</head>
<body>

<section class="card card--front" aria-label="Card front">
  <svg class="front-swoosh" viewBox="0 0 800 457" preserveAspectRatio="none" aria-hidden="true">
    <path d="M300 457 C 570 430, 750 330, 785 0 L 800 0 L 800 457 Z" fill="var(--black)"/>
    <path d="M330 457 C 590 435, 770 340, 800 40 L 800 457 Z" fill="var(--teal)"/>
  </svg>

  <div class="front-brand">Satchel &amp; Sundial</div>
  <div class="front-divider"></div>

  <div class="contact">
    <p class="contact__name">Dorota Falkner</p>
    <p class="contact__role">Your Lifestyle Business Coach,<br>Retreat &amp; Trip Leader</p>
    <ul class="contact__list">
      <li>
        <svg viewBox="0 0 16 16"><path d="M3 1.5l3 .5 1 3-2 1.3a9 9 0 0 0 4.7 4.7L11 9l3 1 .5 3-2 1.5C7 14 2 9 1.5 3.5z" fill="var(--teal)"/></svg>
        +000 12 34 56 7
      </li>
      <li>
        <svg viewBox="0 0 16 16"><rect x="1" y="3" width="14" height="10" fill="var(--teal)"/><path d="M1 3l7 6 7-6" fill="none" stroke="#fff" stroke-width="1.4"/></svg>
        hello@satchelandsundial.example
      </li>
      <li>
        <svg viewBox="0 0 16 16"><circle cx="8" cy="8" r="6.5" fill="none" stroke="var(--teal)" stroke-width="1.5"/><path d="M1.5 8h13M8 1.5c-3 3.5-3 9.5 0 13M8 1.5c3 3.5 3 9.5 0 13" fill="none" stroke="var(--teal)" stroke-width="1.2"/></svg>
        www.satchelandsundial.example
      </li>
    </ul>
    <p class="contact__address">Here your company or<br>home address</p>
  </div>
</section>

<section class="card card--back" aria-label="Card back">
  <div class="back-brand">Satchel &amp; Sundial</div>
  <p class="back-tagline">Live a life you don't need a holiday from</p>
</section>

</body>
</html>
```